Hvac and insulation company needs good looking business card design

We are hvac and insulation company and looking for a new business cards that look to today standards designs

Target Market(s)

homeowners

Industry/Entity Type

Hvac

Contact Information for Business Card

Name: Walter Brinoku
Home comfort consultant
address: 4827 Dunmore St #215 Oakland, CA 94619
office: 888-316-2790
cell: 510-742-3185
Lic.# 584261
Email: walter@corvane-hvac.com
Web: corvane-hvac.com

Requirements
Must have
• clean and sleek look
Nice to have
• simple with a clean look
Should not have
• to busy business card

```html
<!DOCTYPE html>
<html lang="en">
<head>
<meta charset="utf-8">
<title>Corvane Home Solutions – Business Card</title>
<link rel="stylesheet" href="https://fonts.googleapis.com/css2?family=Work+Sans:wght@400;500;600&display=swap">
<style>
  :root {
    --backdrop: #1c1c1d;
    --card: #1a1a1b;
    --card-edge: #262627;
    --accent: #f0851f;
    --ink: #f2f2f2;
    --ink-muted: #9a9a9c;
  }
  * { box-sizing: border-box; margin: 0; padding: 0; }
  html, body { width: 1200px; height: 900px; overflow: hidden; }
  body {
    background: var(--backdrop);
    font-family: "Work Sans", Arial, sans-serif;
    color: var(--ink);
    display: flex;
    flex-direction: column;
    align-items: center;
    justify-content: center;
    gap: 48px;
  }
  .card {
    width: 660px;
    height: 378px;
    background: linear-gradient(135deg, #1e1e1f 0%, var(--card) 60%, #161617 100%);
    border: 1px solid var(--card-edge);
    position: relative;
  }

  /* Back */
  .card-back {
    display: flex;
    flex-direction: column;
    align-items: center;
    justify-content: center;
  }
  .brand-back {
    display: flex;
    align-items: center;
    gap: 18px;
    font-size: 64px;
    font-weight: 500;
    letter-spacing: 1px;
    color: #bdbdbf;
    margin-top: -20px;
  }
  .brand-back .brand-mark {
    width: 46px; height: 46px;
    background: #2b2b2c;
  }
  .licence {
    position: absolute;
    bottom: 46px;
    left: 0; right: 0;
    text-align: center;
    font-size: 17px;
    letter-spacing: 1px;
  }

  /* Front */
  .card-front {
    display: flex;
    align-items: center;
    padding: 0 40px 0 58px;
  }
  .brand-front {
    display: flex;
    align-items: center;
    gap: 12px;
    font-size: 44px;
    font-weight: 500;
    color: var(--accent);
    width: 260px;
  }
  .brand-front .brand-mark {
    width: 34px; height: 34px;
    background: var(--accent);
  }
  .divider {
    width: 2px;
    height: 176px;
    background: var(--accent);
    margin: 0 26px 0 18px;
  }
  .contact { font-size: 16.5px; line-height: 1.3; letter-spacing: 0.3px; }
  .contact-name {
    font-size: 24px;
    font-weight: 500;
    color: var(--accent);
    text-transform: uppercase;
    letter-spacing: 0.5px;
    line-height: 1.1;
  }
  .contact-role { font-size: 17px; margin-bottom: 6px; }
  .contact-address { margin-bottom: 4px; }
  .contact-line { display: flex; align-items: center; gap: 9px; }
  .contact-line svg { width: 11px; height: 11px; flex: none; }
  .web-domain { color: var(--accent); }
</style>
</head>
<body>

  <section class="card card-back" aria-label="Card back">
    <div class="brand-back">
      <span class="brand-mark"></span>
      <span class="brand-name">corvane</span>
    </div>
    <p class="licence">Lic.# 584261</p>
  </section>

  <section class="card card-front" aria-label="Card front">
    <div class="brand-front">
      <span class="brand-mark"></span>
      <span class="brand-name">corvane</span>
    </div>
    <div class="divider"></div>
    <div class="contact">
      <p class="contact-name">Walter Brinoku</p>
      <p class="contact-role">Home comfort consultant</p>
      <p class="contact-address">4827 Dunmore St<br>#215 Oakland, CA 94619</p>
      <p class="contact-line">
        <svg viewBox="0 0 12 12" aria-hidden="true"><path d="M2.5 1 L4.5 1 L5 3.5 L3.8 4.4 Q5 7 7.6 8.2 L8.5 7 L11 7.5 L11 9.5 Q11 11 9.5 11 Q1 10 1 2.5 Q1 1 2.5 1Z" fill="var(--accent)"/></svg>
        888-316-2790
      </p>
      <p class="contact-line">
        <svg viewBox="0 0 12 12" aria-hidden="true"><rect x="3" y="0.8" width="6" height="10.4" rx="1" fill="none" stroke="var(--accent)" stroke-width="1.3"/><circle cx="6" cy="9.3" r="0.7" fill="var(--accent)"/></svg>
        510-742-3185
      </p>
      <p class="contact-line">
        <svg viewBox="0 0 12 12" aria-hidden="true"><rect x="0.8" y="2.5" width="10.4" height="7" fill="none" stroke="var(--accent)" stroke-width="1.2"/><path d="M0.8 2.5 L6 6.5 L11.2 2.5" fill="none" stroke="var(--accent)" stroke-width="1.2"/></svg>
        walter@corvane-hvac.com
      </p>
      <p class="contact-line">
        <svg viewBox="0 0 12 12" aria-hidden="true"><g fill="none" stroke="var(--accent)" stroke-width="1"><circle cx="6" cy="6" r="5"/><ellipse cx="6" cy="6" rx="2.2" ry="5"/><path d="M1 6 H11 M2 3.3 H10 M2 8.7 H10"/></g></svg>
        <span>www.<span class="web-domain">corvane-hvac</span>.com</span>
      </p>
    </div>
  </section>

</body>
</html>
```